Business card design for holistic health care clinic

We need a double-sided business card design for our holistic health care clinic that integrates our logo design and also its color scheme. My business is called Valmira. It is an integrative medicine clinic. You have already done the logo for me. Please ensure an elegant and upscale design that is not cluttered, but still has all the necessary information (please see below for details).

Target Market(s)

Wellness, fitness, rehabilitation for educated, well-traveled open-minded clients who are focused on natural, organic, balanced and preventive healthcare and lifestyle.

Industry/Entity Type

Medical

Contact Information for Business Card

Modern, clean.

Number of Pages Required

1 page

Font styles to use
Serif
Sans Serif

Colors

Designer to choose colors to be used in the design.

Requirements
Must have
• Logo on one side, all other information on the other side.
• Other information should include:
• Tobias Wrenfeld - DOE, CPT, LMT
• 4100 East Marrow Drive
• Austin, TX 78119
• 512 555 0148
• 818 555 0192
• info@ValmiraHealth.example
• t.wrenfeld@ValmiraHealth.example
Nice to have
• Darker background on front - but not totally black - shaded/dark gray.

```html
<!DOCTYPE html>
<html lang="en">
<head>
<meta charset="utf-8">
<title>Valmira Business Card</title>
<link href="https://fonts.googleapis.com/css2?family=Nunito:wght@700;800&family=Roboto:ital,wght@0,400;1,400&family=Roboto+Condensed:wght@700&display=swap" rel="stylesheet">
<style>
  :root {
    --backdrop: #5a4838;
    --card-top: #242424;
    --card-bottom: #303030;
    --brand-blue: #0a8fc8;
    --text-light: #ececec;
    --band-text: #f2f2f2;
  }
  * { margin: 0; padding: 0; box-sizing: border-box; }
  html, body {
    width: 1200px;
    height: 960px;
    overflow: hidden;
    background: var(--backdrop);
  }
  .canvas {
    position: relative;
    width: 1200px;
    height: 960px;
  }
  .card {
    position: absolute;
    border-radius: 18px;
    background: linear-gradient(180deg, var(--card-top), var(--card-bottom));
    overflow: hidden;
  }
  .card--front { left: 314px; top: 113px; width: 602px; height: 343px; }
  .card--back  { left: 311px; top: 472px; width: 600px; height: 342px; }

  .brand-display {
    position: absolute;
    left: 22px;
    top: 40px;
    font-family: "Nunito", sans-serif;
    font-weight: 800;
    font-size: 76px;
    letter-spacing: 2px;
    color: var(--brand-blue);
    line-height: 1;
  }

  .person {
    position: absolute;
    right: 30px;
    top: 174px;
    font-family: "Roboto Condensed", sans-serif;
    font-weight: 700;
    color: var(--brand-blue);
    white-space: nowrap;
  }
  .person__name { font-size: 19px; }
  .person__credentials { font-size: 11px; }

  .contact-list {
    position: absolute;
    right: 30px;
    top: 211px;
    list-style: none;
    font-family: "Roboto", sans-serif;
    font-size: 14px;
    color: var(--text-light);
    text-align: right;
  }
  .contact-list li {
    height: 19px;
    line-height: 19px;
    display: flex;
    justify-content: flex-end;
    align-items: center;
    gap: 6px;
  }
  .contact-list svg { width: 13px; height: 13px; fill: var(--brand-blue); flex: none; }

  .address {
    position: absolute;
    right: 30px;
    top: 296px;
    font-family: "Roboto", sans-serif;
    font-size: 14.5px;
    color: var(--text-light);
  }

  .logo-block {
    position: absolute;
    left: 0;
    right: 0;
    top: 140px;
    text-align: center;
    color: var(--brand-blue);
  }
  .logo-block__name {
    font-family: "Nunito", sans-serif;
    font-weight: 800;
    font-size: 66px;
    line-height: 1;
    letter-spacing: 1px;
  }
  .logo-block__descriptor {
    margin-top: 2px;
    font-family: "Nunito", sans-serif;
    font-weight: 700;
    font-size: 17.5px;
  }

  .tagline-band {
    position: absolute;
    left: 0;
    right: 0;
    bottom: 0;
    height: 30px;
    background: var(--brand-blue);
    text-align: center;
    font-family: "Roboto", sans-serif;
    font-style: italic;
    font-size: 17px;
    line-height: 31px;
    color: var(--band-text);
  }
</style>
</head>
<body>
<main class="canvas">

  <section class="card card--front" aria-label="Business card, contact side">
    <div class="brand-display">VALMIRA</div>

    <p class="person">
      <span class="person__name">TOBIAS WRENFELD</span>
      <span class="person__credentials">- DOE, CPT, LMT</span>
    </p>

    <ul class="contact-list">
      <li>512 555 0148
        <svg viewBox="0 0 24 24" aria-hidden="true"><path d="M6.6 10.8a15.1 15.1 0 0 0 6.6 6.6l2.2-2.2c.3-.3.7-.4 1-.2 1.1.4 2.3.6 3.6.6.6 0 1 .4 1 1V20c0 .6-.4 1-1 1A17 17 0 0 1 3 4c0-.6.4-1 1-1h3.5c.6 0 1 .4 1 1 0 1.3.2 2.5.6 3.6.1.3 0 .7-.2 1z"/></svg>
      </li>
      <li>818 555 0192
        <svg viewBox="0 0 24 24" aria-hidden="true"><path d="M7 1h10a2 2 0 0 1 2 2v18a2 2 0 0 1-2 2H7a2 2 0 0 1-2-2V3a2 2 0 0 1 2-2zm0 3v14h10V4zm5 15.2a1.2 1.2 0 1 0 0 2.4 1.2 1.2 0 0 0 0-2.4z"/></svg>
      </li>
      <li>t.wrenfeld@ValmiraHealth.example
        <svg viewBox="0 0 24 24" aria-hidden="true"><path d="M2 5h20v14H2zm2 2v.4l8 5 8-5V7zm0 2.8V17h16V9.8l-8 5z"/></svg>
      </li>
      <li>www.ValmiraHealth.example
        <svg viewBox="0 0 24 24" aria-hidden="true"><path d="M12 2a10 10 0 1 0 0 20 10 10 0 0 0 0-20zm-1 17.9A8 8 0 0 1 4.2 10L9 14.8v1a2 2 0 0 0 2 2zm6.9-2.5A2 2 0 0 0 16 16h-1v-3a1 1 0 0 0-1-1H8v-2h2a1 1 0 0 0 1-1V7h2a2 2 0 0 0 2-2v-.4a8 8 0 0 1 2.9 12.8z"/></svg>
      </li>
    </ul>

    <p class="address">4100 East Marrow Drive, Austin, TX 78119</p>
  </section>

  <section class="card card--back" aria-label="Business card, brand side">
    <div class="logo-block">
      <div class="logo-block__name">VALMIRA</div>
      <div class="logo-block__descriptor">Integrative Holistic Medicine</div>
    </div>
    <div class="tagline-band">helping the body help itself</div>
  </section>

</main>
</body>
</html>
```